SaaS / Consulting / Solution website redesign

We need a website design that:
- Is completely different than our current design : https://plumvessel.net
- Has a very minimal amount of copy
- Changes our positioning from a SaaS application to a solutions company. Solutions company means that we help our customers solve their problems with consulting, training, and tools. An example of a solutions company is here: https://oldpages.example/web/20130111103320/http://www.brindlework.com:80/
- Does not make us look like a start up
- Is more people oriented than technology oriented

We need a designer that:
- Is a rebel at heart
- Is a minimalist
- Tells us why our current site sucks
- Can disagree with us
- Can also do copywriting or already has a copywriter that can help
- Is ok with saying we have capability that we don't in order to see if people actually want that
- Can understand the difference between our grand vision and where we need to focus ourselves today in order to get there

Who we are:
- Entrepreneurs
- Programmers
- Consultants
- Investors

Here's our design goals:
#1 Get customers, investors, employers, and partners excited about our unique and clearly articulated value proposition
#2 Get people to contact us asking for help with their programs
#3 Position ourselves as an expert in the skills based volunteering, mentorship, and group collaboration
#4 Make it easy for people, who already know who we are, to register online

What our grand vision is:
- Create a marketplace where any person can go to our site and find time with anyone they need to meet with. Whether that is their hair stylist, school advisor, parent of your kids class, dentist, attorney, etc.

What will you get if you win:
- In addition to the prize of this project we will have many landing pages and other revisions we will need in the future. We currently don't have a designer or copywriter and need to add that capability to our team

Who do we need to appeal to:
- Directors that are launching innovative programs inside organizations
- IT personnel who are trying to disqualify our technology so they don't have to support it or deal with it when it doesn't go well
- Enterprise IT architects who don't want our product being on its own island within their organization totally incompatible with everything else. Architects which are trying to assess how our platform will co-exist with all their other platforms
- Vice Presidents who want to help their directors understand that we don't have enough experience to help them
- Program managers who have to juggle a million things and need a tool that actually helps instead of confuses them and adds more work for them.
- Program managers & directors that have been given ambiguous goals by their board of directors like "improve retention, increase engagement, create innovation, get people to collaborate." And who have no idea where to start or how to deliver on things like that.
- Program managers, directors, and vice presidents that are trying to understand how our technology and services fit into their existing technology and capability
- Employees who are bored and uninspired with their current tools and are hoping for some excitement in their life. Kind of like candy or a double espresso.
- Investors who think, our company like all the rest, are going to waste their money and make them look like a fool

Other information:
-The CSS and html needs to be responsive

-Our registration onboarding flow needs to collect this information:
User first name
user last name
user email
(verify their email)
user phone number
(verify their phone number)
User profile image (optional)
User profile summary (optional, like a bio, freeform text fiels)
If applicable: Register their organization
Organization name
Organization image (optional)
Account Mailing address
account Billing address (could be same as mailing address)
account Billing email address (could be same as user address)
account Product selection (pricing tier)
account Credit card information

The designs I am getting are a good start but they are only the front page. I just want you to know that I am expecting and need more than a landing page to complete the design. I will likely need a page that outlines the benefits and features of the product itself, how its different than our competitors, which will not be on the front page. I will need a registration flow. I will need a blog page design so we can post blog articles, I will need a team page, a page that goes into detail on our training, our services. I will likely need a page that shows all news and media we have been in. I need to show customer and user quotes, case studies, a way to contact us, partners, general resources like on collaboration, product tutorials, customers. I need the site to address a comprehensive set of needs. I need that design to be consistent and thorough. I know what PlateHarbor is. I'm not using because I need more than a template that was customized. I need to be unique and match our brand thoughtfully, beautifully, and artistically. Someone asked me a question about how Murmly is similar to our tool in the way it is referred by end users and purchased by managers. Our website needs to primarily talk to the managers as I explained in the brief but it needs to appear cool and exciting to our end-users without focusing on the technology too much. Murmly is a tool that teams use to collaborate in small and large enterprises. The value prop for them is that communication is easier. But they don't put that on their website. Why? Because the users of the technology won't go to the website to find out information on it, they get their information from someone who is using it and demos it to them. When Ines tells her manager Otto "Lets get murmly, Ruth is using it at her company and its great" Ines's manager doesn't know anything about murmly so she promptly googles it. The most important thing from Ines's perspective is that Otto agrees to try it out. Otto's biggest concern is that productivity will be enhanced to degraded. Murmly knows this and so on the front page they know they are talking to Otto NOT Ines because Ines is already sold on it and doesn't need to get sold on the website. Ines is end user. Otto is the purchaser. We have the same problem and so our end users are not the ones purchasing our product, their managers are purchasing our product. We get referred by our end users and vetted by their managers. Hope this helps! Thank you for looking at this project!  Added Wednesday, June 7, 2017

Another observation I am having about the designs being submitted. I believe we used the animations on our current website because animations / cartoons connect with the "inner child" in our users. Whatever that means :-). I think it's what makes our brand fun. I have a hard time imagining that we could make the design fun looking without animations but I'm sure it can be achieved. I also recognize that blending pictures of real people and animations is hard. So either we must masterfully blend them, use only animations, or make the real people have a LOT of fun! So far most of the designs while achieve the goal of appealing to the serious Vice Presidents and directors, they are not doing a good job at appealing to the overworked program managers and bored employees. There seems to stand another challenge with animations which is animations are hard to find and/or create that achieve the message / emotion we are trying to communicate. I don't have any good answers for this but I will say we can hire both animators and illustrators if we need to. All you have to do is communicate the effect in the website design with some simpler version maybe not the end illustration or animation itself. Added Wednesday, June 7, 2017

• Sex appeal and a sense of humor. Copy that makes people excited and clairvoyant about our potential.
• Boring renditions of other non-inspiring websites

```html
<!DOCTYPE html>
<html lang="en">
<head>
<meta charset="utf-8">
<title>Plumvessel</title>
<link rel="stylesheet" href="https://fonts.googleapis.com/css2?family=Montserrat:wght@500;600;700;800&family=Open+Sans:wght@400;600;700&display=swap">
<style>
:root{
  --ink:#444444;
  --text:#555555;
  --dark:#4a4a4a;
  --darker:#3f3f3f;
  --light:#f5f5f5;
  --red:#ef5656;
  --blue:#3daee9;
  --green:#87d07f;
  --green-shade:#6bb663;
  --yellow:#fcdc5f;
  --white:#ffffff;
  --line:#dddddd;
}
*{box-sizing:border-box;margin:0;padding:0}
html,body{width:1200px;height:2439px;overflow:hidden;background:var(--white)}
body{position:relative;font-family:'Open Sans',Arial,sans-serif;color:var(--text)}
.abs{position:absolute}
h1,h2,h3,h4,.brand,.nav a,.btn{font-family:'Montserrat',Arial,sans-serif}

/* header */
.site-header{left:0;top:0;width:1200px;height:70px;background:var(--white)}
.brand{left:75px;top:12px;font-size:35px;font-weight:700;color:var(--ink);letter-spacing:.5px}
.nav{left:428px;top:24px;display:flex}
.nav a{display:block;font-size:12.5px;font-weight:600;color:var(--ink);text-decoration:none;padding:4px 18px 8px;letter-spacing:.3px}
.nav a.active{color:var(--blue);border-bottom:2px solid var(--blue)}

/* hero */
.hero{left:0;top:70px;width:1200px;height:494px;overflow:hidden}
.hero-photo{position:absolute;inset:0;background:linear-gradient(100deg,#8d8a86 0%,#b9b2a9 25%,#d8d2c8 50%,#b4b6b9 72%,#7f8387 100%)}
.hero-shade{position:absolute;inset:0;background:rgba(60,60,66,.35)}
.hero h1{position:absolute;left:0;width:1200px;top:163px;text-align:center;font-size:47px;font-weight:800;color:var(--white);letter-spacing:1px}
.hero p{position:absolute;left:180px;width:840px;top:223px;text-align:center;font-size:16.5px;font-weight:700;line-height:26px;color:var(--white)}
.btn{display:flex;align-items:center;justify-content:center;font-weight:600;color:var(--white);text-transform:uppercase;letter-spacing:.5px}
.btn-green{background:var(--green);box-shadow:inset 0 -3px 0 var(--green-shade)}
.hero .btn{left:524px;top:297px;width:151px;height:47px;font-size:13px}
.dots{left:565px;top:454px;display:flex;gap:8px}
.dots span{width:11px;height:11px;border-radius:50%;background:var(--white)}
.dots span.on{background:var(--red)}

/* about */
.about h2,.news h2,.testimonials h2{font-size:24px;font-weight:600;color:var(--ink);letter-spacing:.3px}
.about h2{left:75px;top:610px}
.about p{left:75px;top:652px;width:695px;font-size:13.9px;line-height:25.6px;color:var(--text)}
.about .btn{left:75px;top:810px;width:151px;height:43px;font-size:13px}
.finder{left:793px;top:615px;width:320px;height:237px;background:var(--dark);border:2px solid var(--darker)}
.finder h3{position:absolute;left:21px;top:23px;font-size:24px;font-weight:600;color:var(--white);letter-spacing:.3px}
.field{position:absolute;left:20px;width:280px;height:37px;background:var(--white);border-radius:2px;font-size:11.5px;color:var(--ink);padding:11px 14px}
.field svg{position:absolute;right:12px;top:12px}
.finder .f1{top:69px}
.finder .f2{top:120px}
.finder .btn{left:20px;top:167px;width:280px;height:48px;font-size:15px}

/* we are */
.we-are{left:0;top:896px;width:1200px;height:471px;background:var(--light)}
.we-are h2{position:absolute;left:0;width:1200px;top:45px;text-align:center;font-size:24px;font-weight:600;color:var(--ink)}
.we-are .lead{position:absolute;left:0;width:1200px;top:91px;text-align:center;font-size:13.5px;color:var(--text)}
.roles{position:absolute;left:75px;top:146px;width:1052px;height:280px;display:flex}
.role{width:263px;height:280px;text-align:center;color:var(--white)}
.role-icon{display:block;margin:28px auto 0;width:100px;height:74px}
.role h3{margin-top:20px;font-size:17px;font-weight:600;letter-spacing:.5px}
.role p{margin:12px auto 0;width:218px;font-size:13.5px;line-height:22.5px;color:rgba(255,255,255,.92)}
.r1{background:var(--red)}.r2{background:var(--blue)}.r3{background:var(--green)}.r4{background:var(--yellow)}

/* mission */
.panel{top:1418px;width:513px;height:254px;background:linear-gradient(125deg,#4c4c4c 0%,#555 35%,#474747 60%,#515151 100%);text-align:center;color:var(--white)}
.panel h3{margin-top:60px;font-size:24px;font-weight:600;letter-spacing:.5px}
.panel p{margin:8px auto 0;width:420px;font-size:14px;line-height:24px}
.mission{left:75px}.vision{left:614px}

/* news & testimonials */
.stories{left:0;top:1740px;width:1200px;height:450px;background:linear-gradient(180deg,#f1f1f1 0%,#fbfbfb 100%)}
.news h2{left:75px;top:1784px}
.testimonials h2{left:628px;top:1784px}
.divider{left:600px;top:1789px;width:1px;height:325px;background:var(--line)}
.news-item{left:75px;width:500px;height:112px}
.news-item .thumb{position:absolute;left:0;top:0;width:179px;height:112px}
.news-item h4{position:absolute;left:200px;top:-2px;width:300px;font-size:12.5px;line-height:21px;font-weight:700;color:var(--blue);text-transform:uppercase}
.news-item p{position:absolute;left:200px;top:44px;width:290px;font-size:13.6px;line-height:23px}
.n1{top:1844px}.n2{top:2000px}
.n1 .thumb{background:linear-gradient(135deg,#b8a48a,#7e8ea1)}
.n2 .thumb{background:linear-gradient(135deg,#c8c9a6,#4e6b4d)}
.quote{left:628px;width:500px}
.quote .mark{position:absolute;left:0;top:8px;width:35px;height:35px;border-radius:50%;background:var(--red)}
.quote .mark svg{position:absolute;left:10px;top:11px}
.quote p{position:absolute;left:49px;top:0;width:455px;font-size:13.8px;line-height:23px}
.quote .name{position:absolute;left:49px;top:101px;font-size:13px;font-weight:700;color:var(--red)}
.q1{top:1838px}.q2{top:1992px}

/* newsletter */
.newsletter{left:0;top:2190px;width:1200px;height:96px;background:var(--blue)}
.newsletter h3{position:absolute;left:252px;top:34px;font-size:24px;font-weight:600;color:var(--white);letter-spacing:.3px}
.newsletter .input{position:absolute;left:548px;top:25px;width:268px;height:48px;background:var(--white);font-size:11.5px;color:var(--ink);padding:17px 17px}
.newsletter .btn{position:absolute;left:831px;top:25px;width:115px;height:48px;background:var(--red);font-size:15px}

/* footer */
.site-footer{left:0;top:2286px;width:1200px;height:153px;background:var(--dark);color:var(--white)}
.foot-nav{position:absolute;left:0;width:1200px;top:42px;display:flex;justify-content:center;gap:40px;font-size:12px;letter-spacing:.3px}
.copyright{position:absolute;left:0;width:1200px;top:74px;text-align:center;font-size:11px}
.social{position:absolute;left:0;width:1200px;top:107px;display:flex;justify-content:center;gap:28px}
.social span{width:14px;height:14px;border-radius:3px;border:2px solid var(--white)}
</style>
</head>
<body>

<header class="site-header abs">
  <div class="brand abs">Plumvessel</div>
  <nav class="nav abs">
    <a class="active">HOME</a><a>ABOUT US</a><a>SERVICES</a><a>SOLUTION</a><a>BLOG</a><a>NEWS</a><a>CONTACT US</a>
  </nav>
</header>

<section class="hero abs">
  <div class="hero-photo" role="img" aria-label="Photo of smiling business people shaking hands across an office table"></div>
  <div class="hero-shade"></div>
  <h1>WELCOME TO PLUMVESSEL</h1>
  <p>We are a Saas company and want to to a solutions company. Solutions company means that we help our customers solve their problems with consulting, training, and tools.</p>
  <div class="btn btn-green abs">GET STARTED</div>
  <div class="dots abs"><span class="on"></span><span></span><span></span><span></span></div>
</section>

<section class="about">
  <h2 class="abs">ABOUT OUR COMPANY</h2>
  <p class="abs">Aliquam molestie, mi et imperdiet euismod, dui purus auctor tellus, et interdum lacus lectus et ante. Sed accumsan sollicitudin sapien, sit amet adipiscing turpis gravida ac. In congue, neque ac lobortis volutpat, libero mauris varius mi, vitae suscipit ipsum ligula vitae risus. Duis aliquam nibh a dui iaculis viverra id a velit. Vivamus egestas risus in magna varius commodo. Sed semper viverra egestas. Etiam pretium porttitor lectus, vel ornare neque porta volutpat....</p>
  <div class="btn btn-green abs">READ MORE</div>
  <div class="finder abs">
    <h3>FIND SOLUTION</h3>
    <div class="field f1">Select Category
      <svg width="8" height="12" viewBox="0 0 8 12"><path d="M4 0L8 5H0z M4 12L0 7H8z" fill="#333"/></svg>
    </div>
    <div class="field f2">Select Time
      <svg width="12" height="12" viewBox="0 0 12 12"><circle cx="6" cy="6" r="5" fill="none" stroke="#333" stroke-width="1.4"/><path d="M6 3v3.3l2 1.2" fill="none" stroke="#333" stroke-width="1.2"/></svg>
    </div>
    <div class="btn btn-green abs">SEARCH</div>
  </div>
</section>

<section class="we-are abs">
  <h2>WE ARE</h2>
  <p class="lead">Aliquam molestie, mi et imperdiet euismod, dui purus auctor tellus, et interdum lacus lectus et ante.</p>
  <div class="roles">
    <div class="role r1">
      <svg class="role-icon" viewBox="0 0 100 74" role="img" aria-label="Icon of a group of people">
        <g fill="#fff">
          <circle cx="28" cy="22" r="10"/><path d="M10 62c0-14 8-22 18-22s18 8 18 22z"/>
          <circle cx="72" cy="22" r="10"/><path d="M54 62c0-14 8-22 18-22s18 8 18 22z"/>
          <circle cx="50" cy="18" r="12" stroke="#ef5656" stroke-width="2"/><path d="M27 66c0-17 10-27 23-27s23 10 23 27z" stroke="#ef5656" stroke-width="2"/>
        </g>
      </svg>
      <h3>ENTREPRENEURS</h3><p>Sed accumsan sollicitudin sapien, sit amet adipiscing turpis gravida ac lobortis turpis in odio blandit ..</p></div>
    <div class="role r2">
      <svg class="role-icon" viewBox="0 0 100 74" role="img" aria-label="Icon of a person working at a computer desk">
        <g fill="#fff">
          <circle cx="32" cy="14" r="8"/><path d="M22 26h18v20H22z"/><path d="M22 44h22v6H28v16h-6z"/>
          <rect x="56" y="16" width="22" height="18" rx="2"/><rect x="65" y="34" width="4" height="8"/>
          <rect x="44" y="42" width="46" height="4"/><rect x="48" y="46" width="3" height="22"/><rect x="83" y="46" width="3" height="22"/>
        </g>
      </svg>
      <h3>PROGRAMMERS</h3><p>Sed accumsan sollicitudin sapien, sit amet adipiscing turpis gravida ac lobortis turpis in odio blandit ..</p></div>
    <div class="role r3">
      <svg class="role-icon" viewBox="0 0 100 74" role="img" aria-label="Icon of people meeting around a table">
        <g fill="#fff">
          <circle cx="50" cy="12" r="8"/><path d="M38 36c0-10 5-14 12-14s12 4 12 14z"/>
          <circle cx="16" cy="30" r="8"/><path d="M4 62c0-14 5-20 12-20s12 6 12 20z"/>
          <circle cx="84" cy="30" r="8"/><path d="M72 62c0-14 5-20 12-20s12 6 12 20z"/>
          <rect x="30" y="40" width="40" height="24" rx="3"/>
        </g>
      </svg>
      <h3>CONSULTANTS</h3><p>Sed accumsan sollicitudin sapien, sit amet adipiscing turpis gravida ac lobortis turpis in odio blandit ..</p></div>
    <div class="role r4">
      <svg class="role-icon" viewBox="0 0 100 74" role="img" aria-label="Icon of two investors with a dollar coin">
        <g fill="#fff">
          <circle cx="36" cy="34" r="9"/><path d="M18 70c0-15 8-22 18-22s18 7 18 22z"/>
          <circle cx="64" cy="34" r="9"/><path d="M46 70c0-15 8-22 18-22s18 7 18 22z"/>
          <circle cx="64" cy="12" r="11"/>
        </g>
        <path d="M68 7h-5a2.5 2.5 0 0 0 0 5h2a2.5 2.5 0 0 1 0 5h-5M64 4v16" fill="none" stroke="#fcdc5f" stroke-width="2"/>
      </svg>
      <h3>INVESTORS</h3><p>Sed accumsan sollicitudin sapien, sit amet adipiscing turpis gravida ac lobortis turpis in odio blandit ..</p></div>
  </div>
</section>

<div class="panel mission abs">
  <h3>MISSION</h3>
  <p>Aliquam molestie, mi et imperdiet euismod, dui purus auctor tellus, et interdum lacus lectus et ante. Sed accumsan sollicitudin sapien, sit amet adipiscing turpis gravida ac. In congue, neque ac lobortis volutpat..</p>
</div>
<div class="panel vision abs">
  <h3>VISION</h3>
  <p>Aliquam molestie, mi et imperdiet euismod, dui purus auctor tellus, et interdum lacus lectus et ante. Sed accumsan sollicitudin sapien, sit amet adipiscing turpis gravida ac. In congue, neque ac lobortis volutpat..</p>
</div>

<div class="stories abs"></div>
<section class="news">
  <h2 class="abs">NEWS UPDATES</h2>
  <article class="news-item n1 abs">
    <div class="thumb" role="img" aria-label="Photo of movers carrying furniture from a van"></div>
    <h4>Aliquam molestie, mi et imperdiet euismod dui iaculis viverra.</h4>
    <p>Dui purus auctor tellus, et interdum lacus lectus et ante nibh eget turpis vehicula tempus ac sed massa...</p>
  </article>
  <article class="news-item n2 abs">
    <div class="thumb" role="img" aria-label="Photo of cleaning staff at work in a home"></div>
    <h4>Aliquam molestie, mi et imperdiet euismod dui iaculis viverra.</h4>
    <p>Dui purus auctor tellus, et interdum lacus lectus et ante nibh eget turpis vehicula tempus ac sed massa...</p>
  </article>
</section>
<div class="divider abs"></div>
<section class="testimonials">
  <h2 class="abs">CUSTOMER SAYS</h2>
  <blockquote class="quote q1 abs">
    <span class="mark"><svg width="15" height="13" viewBox="0 0 15 13"><path d="M0 6h4L2 13h3l3-7V0H0z M7 6h4L9 13h3l3-7V0H7z" fill="#fff"/></svg></span>
    <p>Dui purus auctor tellus, et interdum lacus lectus et ante nibh eget turpis vehicula tempus ac sed massa primis in faucibus orci luctus et ultrices posuere vel metus sit amet turpis bibendum tincidunt vel sit amet quam.</p>
    <span class="name">-Name Heading</span>
  </blockquote>
  <blockquote class="quote q2 abs">
    <span class="mark"><svg width="15" height="13" viewBox="0 0 15 13"><path d="M0 6h4L2 13h3l3-7V0H0z M7 6h4L9 13h3l3-7V0H7z" fill="#fff"/></svg></span>
    <p>Dui purus auctor tellus, et interdum lacus lectus et ante nibh eget turpis vehicula tempus ac sed massa primis in faucibus orci luctus et ultrices posuere vel metus sit amet turpis bibendum tincidunt vel sit amet quam.</p>
    <span class="name">-Name Heading</span>
  </blockquote>
</section>

<section class="newsletter abs">
  <h3>NEWSLETTER SIGN UP</h3>
  <div class="input">Enter Email Address</div>
  <div class="btn">SIGN UP</div>
</section>

<footer class="site-footer abs">
  <div class="foot-nav"><span>HOME</span><span>ABOUT US</span><span>SERVICES</span><span>SOLUTION</span><span>BLOG</span><span>NEWS</span><span>CONTACT US</span></div>
  <div class="copyright">Copyright © 2017.Company Name. All Right Reserved</div>
  <div class="social" aria-label="Social links"><span></span><span></span><span></span><span></span><span></span><span></span></div>
</footer>

</body>
</html>
```